Resposive web site in 4 languages + image gallery + logo design

We need a web page, which will work on all devices.
I have uploaded web page concept.
Company name: Praxelun
Industry/Entity Type
It Company
Logo Text
quality matters
Coding
Coded - Design and coding required
Number of Pages Required
1 page

```html
<!DOCTYPE html>
<html lang="en">
<head>
<meta charset="utf-8">
<title>Praxelun</title>
<link href="https://fonts.googleapis.com/css2?family=Questrial&family=Lato:wght@400;700&display=swap" rel="stylesheet">
<style>
:root{
  --blue:#1a7fd4;
  --blue-dark:#0f6cc0;
  --green:#5cbf3a;
  --ink:#1f1f1f;
  --text:#333;
  --muted:#f4f4f4;
  --line:#d9d9d9;
  --footer:#0c0c0c;
  --footer-bottom:#050505;
}
*{margin:0;padding:0;box-sizing:border-box}
html,body{width:1200px;height:2795px;overflow:hidden}
body{position:relative;background:#fff;font-family:"Lato",sans-serif;color:var(--text)}
.abs{position:absolute}
.heading{font-family:"Questrial",sans-serif;font-weight:400}

/* header */
.site-header{left:0;top:0;width:1200px;height:130px;background:#fff}
.brand{left:62px;top:42px;display:flex;align-items:center;gap:12px}
.brand-mark{width:22px;height:22px;background:var(--green)}
.brand-name{font-family:"Questrial",sans-serif;font-size:36px;color:var(--ink)}
.social-top{left:840px;top:20px;display:flex;gap:8px}
.social-top span{width:26px;height:26px;border-radius:50%;background:var(--blue)}
.social-top span:nth-child(3){background:#d9483b}
.social-top span:nth-child(4){background:#e8862a}
.lang{left:1000px;top:15px;width:140px;height:37px;border:1px solid #999;display:flex;align-items:center;padding:0 10px;gap:10px;font-size:15px;color:#222}
.lang .flag{width:34px;height:22px;background:#2b3f8c}
.nav{top:80px;left:0;width:1200px;height:50px}
.nav a{position:absolute;top:2px;font-size:15px;color:#222;text-decoration:none;letter-spacing:.3px}
.nav a.active{color:var(--blue)}
.nav .sep{position:absolute;top:0;width:1px;height:22px;background:#ccc}
.nav .bar{position:absolute;left:615px;top:46px;width:56px;height:3px;background:var(--blue)}

/* hero */
.hero{left:0;top:130px;width:1200px;height:462px;background:linear-gradient(160deg,#5a5a62 0%,#9c8a72 40%,#c2a27a 60%,#8a7a68 100%)}
.hero-title{left:0;top:180px;width:1200px;text-align:center;color:#fff;font-size:38px}
.hero-sub{left:300px;top:250px;width:600px;text-align:center;color:#fff;font-size:15px;line-height:21px}
.dots{left:578px;top:420px;display:flex;gap:6px}
.dots span{width:11px;height:11px;border-radius:50%;background:#fff}
.dots span:first-child{background:var(--blue)}

/* quote band */
.quote{left:0;top:592px;width:1200px;height:135px;background:#fff;border-top:3px solid var(--line);border-bottom:3px solid var(--line)}
.quote-text{left:62px;top:44px;font-size:35px;color:var(--ink)}
.btn-quote{left:935px;top:43px;width:205px;height:46px;border-radius:23px;background:var(--green);color:#fff;font-weight:700;font-size:19px;letter-spacing:.5px;display:flex;align-items:center;justify-content:center}

/* services */
.band{left:0;width:1200px}
.band.grey{background:var(--muted)}
.section-title{left:0;top:750px;width:1200px;text-align:center;font-size:35px;color:var(--ink)}
.section-title em{font-style:normal;color:var(--blue)}
.title-rule{left:571px;top:794px;width:56px;height:3px;background:var(--blue)}
.photo{border:2px solid #c8c8c8}
.service-name{font-size:27px;color:var(--ink)}
.service-text{font-size:14px;line-height:29.4px;color:var(--text)}
.btn-more{height:38px;border-radius:19px;background:var(--blue);color:#fff;font-weight:700;font-size:14px;display:flex;align-items:center;justify-content:center}
.tabs{display:flex;gap:30px;font-size:16px;color:#333}
.tabs span.active{color:var(--blue);border-bottom:2px solid var(--blue);padding-bottom:2px}

/* about */
.about{left:0;top:2083px;width:1200px;height:350px;background:linear-gradient(135deg,#2c2c2c 0%,#4a4640 50%,#2f2f2f 100%)}
.about-title{left:0;top:45px;width:1226px;text-align:center;font-size:35px;color:#fff}
.about-rule{left:498px;top:85px;width:196px;height:2px;background:#ddd}
.about-brand{left:112px;top:170px;display:flex;align-items:center;gap:14px}
.about-brand .brand-mark{width:30px;height:30px}
.about-brand .brand-name{color:#fff;font-size:46px}
.about-divider{left:432px;top:121px;width:3px;height:181px;background:var(--blue)}
.about-text{left:486px;top:112px;width:660px;color:#eee;font-size:14px;line-height:22px}
.about-sign{left:486px;top:265px;color:#fff;font-size:15px;line-height:23px}

/* footer */
.footer{left:0;top:2433px;width:1200px;height:306px;background:var(--footer)}
.footer h3{position:absolute;top:44px;font-family:"Questrial",sans-serif;font-weight:400;font-size:28px;color:#fff}
.footer h3 em{font-style:normal;color:var(--blue)}
.quick-links{left:62px;top:96px;list-style:none;font-size:13px;color:#fff}
.quick-links li{height:32.5px;position:relative;padding-left:14px}
.quick-links li::before{content:"";position:absolute;left:0;top:5px;border-left:5px solid #aaa;border-top:3px solid transparent;border-bottom:3px solid transparent}
.contact-item{display:flex;align-items:flex-start;gap:14px;color:#fff;font-size:14px;line-height:18px}
.contact-item svg{flex:none}
.field{position:absolute;left:639px;width:287px;border:1px solid #bbb;border-radius:3px;color:#ccc;font-size:12px;padding:6px 10px}
.btn-submit{left:635px;top:246px;width:155px;height:41px;border:2px solid var(--blue);border-radius:20px;color:var(--blue);font-weight:700;font-size:15px;display:flex;align-items:center;justify-content:center}
.follow{left:1008px;top:96px;list-style:none;font-size:13px;color:#fff}
.follow li{display:flex;align-items:center;gap:10px;height:35.7px}
.follow li span{width:20px;height:20px;background:#fff}
.copyright{left:0;top:2739px;width:1200px;height:56px;background:var(--footer-bottom);color:#ddd;font-size:13px;display:flex;align-items:center;justify-content:center}
</style>
</head>
<body>

<header class="abs site-header">
  <div class="abs brand"><span class="brand-mark"></span><span class="brand-name">Praxelun</span></div>
  <div class="abs social-top"><span></span><span></span><span></span><span></span></div>
  <div class="abs lang"><span class="flag"></span>English
    <svg width="12" height="8" viewBox="0 0 12 8"><path d="M0 0h12L6 8z" fill="#222"/></svg></div>
  <nav class="abs nav">
    <a class="active" style="left:620px">HOME</a>
    <span class="sep" style="left:716px"></span>
    <a style="left:745px">SERVICES</a>
    <span class="sep" style="left:858px"></span>
    <a style="left:892px">ABOUT US</a>
    <span class="sep" style="left:1015px"></span>
    <a style="left:1064px">CONTACT</a>
    <span class="bar"></span>
  </nav>
</header>

<section class="abs hero" role="img" aria-label="Carpenter laying wooden floor boards with a hammer and handle in the foreground">
  <h1 class="abs heading hero-title">Welcome to Praxelun</h1>
  <p class="abs hero-sub">At vero eos et accusamus et iusto odio dignissimos ducimus qui blanditiis praesentium voluptatum deleniti atque corrupti quos dolores et quas</p>
  <div class="abs dots"><span></span><span></span><span></span></div>
</section>

<section class="abs quote">
  <h2 class="abs heading quote-text">Are you interested in an estimate?</h2>
  <div class="abs btn-quote">GET A QUOTE</div>
</section>

<!-- services -->
<div class="abs band grey" style="top:730px;height:494px"></div>
<h2 class="abs heading section-title">Our <em>Services</em></h2>
<div class="abs title-rule"></div>

<div class="abs photo" style="left:62px;top:857px;width:452px;height:298px;background:linear-gradient(135deg,#b07a4e,#d9c23a 45%,#8a6a50)" role="img" aria-label="Builders in hard hats working on wooden stairs, with gallery thumbnails"></div>
<h3 class="abs heading service-name" style="left:546px;top:862px">Woodworks</h3>
<p class="abs service-text" style="left:546px;top:905px;width:570px">Timber is, in essence, a natural and warm material. Wood is also relatively durable and easy to workwith, which has made it a favourite of builders throughout history. Our goal is to offer GALLERY (sliders) suitable products and quality furniture with installation and after - When cliked opens sales service to all of our clients. In order to achieve this, we're this category gallery ready to help our clients in all stages of construction from design to production and maintenance.</p>
<div class="abs btn-more" style="left:548px;top:1093px;width:139px">READ MORE</div>
<div class="abs tabs" style="left:309px;top:1178px"><span class="active">Furniture</span><span>Windows</span><span>Doors</span><span>Staircases</span><span>Woodcarving</span><span>Graining</span></div>

<div class="abs band" style="top:1224px;height:428px;background:#fff"></div>
<h3 class="abs heading service-name" style="left:62px;top:1296px">STONEWORKS</h3>
<p class="abs service-text" style="left:62px;top:1339px;width:570px">The natural stone found in the ground has been used in construction for centuries because of its durability. A structure GALLERY (sliders) built by a skilled craftsman from natural stone is unique, genuine When cliked opens and durable, and perfect for our bracing climate. this category gallery Our experienced craftsmen are ready to help you in all stages of construction from planning to completion.</p>
<div class="abs btn-more" style="left:65px;top:1509px;width:138px">READ MORE</div>
<div class="abs photo" style="left:686px;top:1272px;width:452px;height:298px;background:linear-gradient(135deg,#e8e2d6,#c9b79a 50%,#8d7b66)" role="img" aria-label="Kitchen with stone countertops and cream cabinets, with gallery thumbnails"></div>
<div class="abs tabs" style="left:265px;top:1599px"><span class="active">Walls</span><span>Terraces</span><span>Paths</span><span>Outdoor kitchens</span><span>Fireplaces</span><span>Smokeries</span><span>Fences</span></div>

<div class="abs band grey" style="top:1652px;height:431px"></div>
<div class="abs photo" style="left:62px;top:1699px;width:452px;height:300px;background:linear-gradient(180deg,#cfdbe8,#b9ad98 55%,#7d6f5f)" role="img" aria-label="Historic building facade under scaffolding, with gallery thumbnails"></div>
<h3 class="abs heading service-name" style="left:546px;top:1708px">Restoration</h3>
<p class="abs service-text" style="left:546px;top:1750px;width:570px">It's good to see that fixing old things has become popular again in recent years and people are trying to find ways to preserve GALLERY (sliders) valuable old windows and pieces of furniture before deciding to When cliked opens replace them. It is possible to give a new life to almost any wooden door, Window, piece of furniture or staircase. The extensive experience of our craftsmen will help you achieve the desired result.</p>
<div class="abs btn-more" style="left:548px;top:1937px;width:139px">READ MORE</div>
<div class="abs tabs" style="left:311px;top:2031px"><span class="active">Furniture</span><span>Windows</span><span>Doors</span><span>Staircases</span><span>Floors</span><span>Special Projects</span></div>

<section class="abs about" role="img" aria-label="Darkened photo of a craftsman measuring wood">
  <h2 class="abs heading about-title">About Us</h2>
  <div class="abs about-rule"></div>
  <div class="abs about-brand"><span class="brand-mark"></span><span class="brand-name">Praxelun</span></div>
  <div class="abs about-divider"></div>
  <p class="abs about-text">Praxelun is a company whose business operations include making wooden products, restoration and building structures from natural stone. All of our products are made by craftsmen and specialists who have extensive experience and knowledge in their fields. The products we offer are always handmade and we take the requests and ideas of the specific client into account We always strive to achieve the best possible quality.</p>
  <p class="abs about-sign"><b>Quality matters,</b><br>&nbsp;Praxelun</p>
</section>

<footer class="abs footer">
  <h3 style="left:62px">Quick <em>link</em></h3>
  <ul class="abs quick-links"><li>Home</li><li>About Us</li><li>Services</li><li>Contact Us</li></ul>

  <h3 style="left:324px">Contact <em>Us</em></h3>
  <div class="abs contact-item" style="left:320px;top:92px">
    <svg width="30" height="30" viewBox="0 0 30 30"><circle cx="15" cy="15" r="14" fill="none" stroke="#1a7fd4" stroke-width="2"/><path d="M15 8a5 5 0 0 0-5 5c0 4 5 9 5 9s5-5 5-9a5 5 0 0 0-5-5z" fill="#1a7fd4"/><circle cx="15" cy="13" r="2" fill="#0c0c0c"/></svg>
    <div><b>Praxelun</b><br>Kastani 12 10115 Varel<br>ESTONIA</div>
  </div>
  <div class="abs contact-item" style="left:320px;top:164px;align-items:center">
    <svg width="30" height="30" viewBox="0 0 30 30"><circle cx="15" cy="15" r="14" fill="none" stroke="#1a7fd4" stroke-width="2"/><path d="M10 9l3-1 2 4-2 1.5c.8 2 2.2 3.4 4 4l1.5-2 4 2-1 3c-6 0-11.5-5.5-11.5-11.5z" fill="#1a7fd4"/></svg>
    <span>555.014.2290</span>
  </div>
  <div class="abs contact-item" style="left:320px;top:216px;align-items:center">
    <svg width="30" height="30" viewBox="0 0 30 30"><circle cx="15" cy="15" r="14" fill="none" stroke="#1a7fd4" stroke-width="2"/><rect x="8" y="10" width="14" height="10" fill="#1a7fd4"/><path d="M8 10l7 6 7-6" fill="none" stroke="#0c0c0c" stroke-width="1.4"/></svg>
    <span>sales@praxelun.com</span>
  </div>

  <h3 style="left:643px">Quick <em>Inquiry</em></h3>
  <div class="field" style="top:95px;height:36px">Name</div>
  <div class="field" style="top:138px;height:37px">Phone</div>
  <div class="field" style="top:183px;height:54px">Message</div>
  <div class="abs btn-submit">SUBMIT</div>

  <h3 style="left:1008px">Follow <em>Us</em></h3>
  <ul class="abs follow"><li><span></span>Friendsy</li><li><span></span>Chirper</li><li><span></span>Circlez</li><li><span></span>Linkwork</li></ul>
</footer>

<div class="abs copyright">Copyright © 2016 Praxelun. All Rights Reserved.</div>

</body>
</html>
```